Velmarotix - world unique technology for better life - please let them know who am i at first sight

We need a new business card for company which is a provider of unique crystal based technology suitable for all living being. For more information and final design you can use our brochure (our colours are black and blue from brochure).
We use Verdana font

Industry/Entity Type

Business

Contact Information for Business Card

regular dimension

Font styles to use
Other font styles liked:
• Verdana

Requirements
Must have
• Logo
• name
• function/position
• phone
• mobile
• e-mail
• adress
Nice to have
• inovative design (technology directed)

```html
<!DOCTYPE html>
<html lang="en">
<head>
<meta charset="utf-8">
<title>Velmarotix business card</title>
<link rel="stylesheet" href="https://fonts.googleapis.com/css2?family=Open+Sans:wght@400;600;700&display=swap">
<style>
  :root {
    --ink: #050505;
    --brand-blue: #0a9fe3;
    --sky: #12a3e6;
    --silver: #b9bcc0;
    --paper: #ffffff;
    --text-light: #e9e9e9;
    --backdrop: #eceef0;
  }
  * { box-sizing: border-box; margin: 0; padding: 0; }
  html, body {
    width: 1200px; height: 948px; overflow: hidden;
    background: var(--backdrop);
    font-family: "Open Sans", Verdana, sans-serif;
  }
  .sheet {
    width: 1200px; height: 948px;
    display: flex; flex-direction: column; align-items: center; justify-content: center;
    gap: 60px;
  }
  .card {
    position: relative; width: 620px; height: 354px; overflow: hidden;
    box-shadow: 0 6px 18px rgba(0,0,0,.18);
  }
  /* front */
  .card-front { background: var(--ink); color: var(--text-light); }
  .front-wave { position: absolute; left: 0; bottom: 0; width: 620px; height: 354px; }
  .brand {
    position: absolute; top: 44px; left: 0; right: 0;
    display: flex; align-items: center; justify-content: center; gap: 14px;
  }
  .brand-dot { width: 46px; height: 46px; border-radius: 50%; background: var(--brand-blue); }
  .brand-name {
    font-size: 38px; font-weight: 400; letter-spacing: 1px; color: var(--brand-blue);
  }
  .holder { position: absolute; top: 142px; left: 120px; }
  .holder-name { font-size: 21px; font-weight: 700; color: var(--brand-blue); }
  .holder-role { font-size: 15px; margin-top: 4px; }
  .holder-address { font-size: 14px; margin-top: 10px; line-height: 1.45; }
  .contacts { position: absolute; top: 146px; left: 360px; list-style: none; }
  .contacts li { display: flex; align-items: center; gap: 9px; font-size: 14px; line-height: 1; margin-bottom: 11px; }
  .contacts svg { width: 18px; height: 18px; flex: none; }
  /* back */
  .card-back {
    background: var(--sky); color: var(--paper);
    display: flex; align-items: center; justify-content: center; gap: 18px;
  }
  .back-dot { width: 120px; height: 120px; border-radius: 50%; background: var(--paper); }
  .back-name { font-size: 34px; font-weight: 600; color: var(--paper); }
  .back-web {
    position: absolute; left: 34px; top: 50%;
    transform: translate(-50%, -50%) rotate(-90deg) translateY(0);
    transform-origin: center; font-size: 15px; letter-spacing: 3px; white-space: nowrap;
    margin-left: 14px;
  }
</style>
</head>
<body>
<main class="sheet">
  <section class="card card-front">
    <svg class="front-wave" viewBox="0 0 620 354" aria-hidden="true">
      <path d="M0 262 C140 300 300 250 420 300 C500 332 570 344 620 338 L620 354 L0 354 Z" fill="var(--silver)"/>
      <path d="M0 278 C140 318 300 268 420 318 C500 348 570 356 620 354 L620 354 L0 354 Z" fill="var(--ink)"/>
      <path d="M0 290 C140 330 300 282 420 330 C490 356 560 360 620 354 L0 354 Z" fill="var(--brand-blue)"/>
    </svg>

    <div class="brand">
      <span class="brand-dot"></span>
      <span class="brand-name">Velmarotix</span>
    </div>

    <div class="holder">
      <p class="holder-name">Mira Kovanic</p>
      <p class="holder-role">Founder and CEO</p>
      <p class="holder-address">Street Name, City Name<br>Zipcode-01234</p>
    </div>

    <ul class="contacts">
      <li>
        <svg viewBox="0 0 18 18" aria-hidden="true"><circle cx="9" cy="9" r="9" fill="var(--text-light)"/><path d="M6 5 l2 0 l1 3 l-1.3 1 a6 6 0 0 0 2.3 2.3 l1-1.3 l3 1 v2 a1 1 0 0 1 -1 1 a8 8 0 0 1 -7 -7 a1 1 0 0 1 1-1z" fill="var(--ink)"/></svg>
        <span>014-552-0817</span>
      </li>
      <li>
        <svg viewBox="0 0 18 18" aria-hidden="true"><circle cx="9" cy="9" r="9" fill="var(--text-light)"/><rect x="6" y="4" width="6" height="10" rx="1" fill="var(--ink)"/><rect x="7" y="5.3" width="4" height="6.5" fill="var(--text-light)"/></svg>
        <span>014-552-0818</span>
      </li>
      <li>
        <svg viewBox="0 0 18 18" aria-hidden="true"><circle cx="9" cy="9" r="9" fill="var(--text-light)"/><rect x="4.5" y="6" width="9" height="6.5" fill="var(--ink)"/><path d="M4.5 6 L9 9.6 L13.5 6" stroke="var(--text-light)" stroke-width="1" fill="none"/></svg>
        <span>info@velmarotix.cu</span>
      </li>
      <li>
        <svg viewBox="0 0 18 18" aria-hidden="true"><circle cx="9" cy="9" r="9" fill="var(--text-light)"/><circle cx="9" cy="9" r="5" fill="none" stroke="var(--ink)" stroke-width="1.2"/><ellipse cx="9" cy="9" rx="2.2" ry="5" fill="none" stroke="var(--ink)" stroke-width="1"/><path d="M4 9 H14" stroke="var(--ink)" stroke-width="1"/></svg>
        <span>www.velmarotix.cu</span>
      </li>
    </ul>
  </section>

  <section class="card card-back">
    <span class="back-web">www.velmarotix.cu</span>
    <span class="back-dot"></span>
    <span class="back-name">Velmarotix</span>
  </section>
</main>
</body>
</html>
```